Rapid Pulse Tiny Track Karts

We are looking for a full web site for our race car category that allows us to edit and update some of the content. We would like the site to feel modern and attractive with the following features: 1. Event calender (with the ability for us to update) 2. Social media/ clip wave links 3. photo gallery (with the ability for us to update) 4. Member area with log in access (controlled access) - this area to include access to category regulations for up to 5 types of cars separately 5. Championship ladder for up to 5 different groups 6. sponsor page and sponsors scrolling across bottom of all pages. Please find attached our logo to be used and for reference on color/ style 7. page to show merchandise but no need for a store.

Industry/Entity Type

Motor racing category

Coding

Coded - Design and coding required

Number of Pages Required

5+ page

Colors
0054AA
0677BA
7BADD7
CADEEF
E8F1F8
FFF300
FFF600
FEFA6F
FFFEC7
FFFEE8
EB3D1F
EC4F4E
F09395
F8D3D4
FCEDEE

Requirements
Must have
• Ability to update calender/photo gallery/championship ladder including points/ notice board - Members section

```html
<!DOCTYPE html>
<html lang="en">
<head>
<meta charset="utf-8">
<title>Rapid Pulse Tiny Track Karts</title>
<link href="https://fonts.googleapis.com/css2?family=Audiowide&family=Poppins:wght@400;500;600&display=swap" rel="stylesheet">
<style>
:root{
  --red:#eb3d1f;
  --red-bright:#f21d1d;
  --red-soft:#f09395;
  --black:#000;
  --ink:#111;
  --white:#fff;
  --grey:#8a8a8a;
  --display:"Audiowide", sans-serif;
  --body:"Poppins", sans-serif;
}
*{margin:0;padding:0;box-sizing:border-box}
html,body{width:1200px;height:4471px;overflow:hidden}
body{font-family:var(--body);color:var(--ink);background:var(--white)}
section,header,footer{position:relative;width:1200px}
.abs{position:absolute}
.section-title{position:absolute;left:0;width:1200px;text-align:center;font-family:var(--display);font-size:31px;letter-spacing:1px;color:var(--red)}
.on-dark .section-title{color:var(--white)}

/* Hero */
.hero{height:596px;background:#1b1b1b;overflow:hidden}
.hero-photo{position:absolute;inset:0;background:radial-gradient(ellipse at 48% 70%,#4a4f4c 0%,#2a2c2b 35%,#141414 75%),#141414}
.hero-car{position:absolute;left:250px;top:290px;width:460px;height:190px;border-radius:40px;background:linear-gradient(90deg,#1d2a2b,#2e4a48 45%,#c78634 60%,#22302f);opacity:.85;filter:blur(2px)}
.brand{position:absolute;display:flex;align-items:center;gap:10px;color:var(--white);font-family:var(--body);font-weight:600;font-size:15px;line-height:1.15;text-transform:uppercase}
.brand-mark{width:18px;height:18px;background:var(--red);flex:none}
.hero .brand{left:100px;top:52px;width:210px}
.main-nav{position:absolute;left:360px;top:66px;display:flex;gap:19px}
.main-nav a{color:var(--white);text-decoration:none;font-size:15px;font-weight:500}
.login{position:absolute;left:983px;top:50px;width:115px;height:51px;border-radius:26px;background:var(--red-bright);color:var(--white);font-family:var(--display);font-size:17px;display:flex;align-items:center;justify-content:center}
.welcome{position:absolute;left:676px;top:212px;color:var(--white);font-family:var(--display)}
.welcome small{display:block;font-size:22px;margin-bottom:18px}
.welcome strong{display:block;font-weight:400;font-size:30px;line-height:54px}

/* Calendar */
.calendar{height:663px}
.calendar .section-title{top:75px}
.pill-btn{position:absolute;top:182px;height:51px;border-radius:26px;background:var(--red-bright);color:var(--white);font-family:var(--display);font-size:17px;display:flex;align-items:center;justify-content:center;gap:6px}
.btn-prev{left:328px;width:157px}
.btn-next{left:723px;width:158px}
.month{position:absolute;left:547px;top:196px;font-family:var(--display);font-size:18px}
.cal-grid{position:absolute;left:240px;top:276px;width:721px;display:grid;grid-template-columns:repeat(7,1fr);text-align:center}
.cal-grid .dow{font-family:var(--display);font-size:17px;height:59px}
.cal-grid .day{font-size:15px;height:55.5px}
.cal-grid .muted{color:var(--grey)}
.cal-grid .today span{display:inline-block;width:30px;height:30px;line-height:26px;margin-top:-6px;border:2px dashed var(--red);border-radius:50%;color:var(--red);font-weight:600}

/* About */
.about{height:580px;background:var(--black);color:var(--white)}
.about .section-title{top:58px}
.about-photo{position:absolute;left:172px;top:141px;width:382px;height:382px;border-radius:50%;border:3px solid var(--white);background:radial-gradient(circle at 50% 70%,#4a4a4a,#1e1e1e 60%,#0b0b0b)}
.about-text{position:absolute;left:599px;top:154px;width:500px;font-size:15px;line-height:34.5px}
.outline-btn{position:absolute;left:599px;top:415px;width:202px;height:51px;border-radius:26px;background:var(--white);color:var(--red);font-family:var(--display);font-size:17px;display:flex;align-items:center;justify-content:center;gap:10px}

/* Merchandise */
.merch{height:680px}
.merch .section-title{top:80px}
.merch-card{position:absolute;top:176px;width:318px;text-align:center}
.merch-photo{height:300px;border-radius:10px}
.merch-name{margin-top:32px;font-family:var(--display);font-size:21px;color:var(--red)}
.price{margin:12px auto 0;width:139px;height:44px;border-radius:22px;background:var(--black);color:var(--white);font-family:var(--display);font-size:16px;line-height:44px}
.round-arrow{position:absolute;width:44px;height:44px;border-radius:50%;background:var(--red-bright);display:flex;align-items:center;justify-content:center}

/* Gallery */
.gallery{height:578px;background:var(--black);overflow:hidden}
.gallery .section-title{top:60px}
.gallery-photo{position:absolute;border-radius:10px}
.gallery-arrows{position:absolute;left:1088px;top:3055px}

/* Sponsor */
.sponsor{height:458px}
.sponsor .section-title{top:82px}
.sponsor-box{position:absolute;top:170px;width:185px;height:160px;background:var(--white);border-radius:6px;box-shadow:0 2px 10px rgba(0,0,0,.22);display:flex;align-items:center;justify-content:center}
.dot{position:absolute;top:386px;width:33px;height:7px;border-radius:4px;background:var(--red-soft)}
.dot.active{background:var(--red-bright)}

/* Championship */
.ladder{height:549px}
.ladder .section-title{top:34px}
.ladder-photo{position:absolute;left:129px;top:116px;width:378px;height:349px;border-radius:10px;background:linear-gradient(180deg,#d9dde0,#8c9aa6 55%,#3b4b5c)}
.ladder-info{position:absolute;left:566px;font-size:18px}
.ladder-info b{font-family:var(--display);font-weight:400;color:var(--red);font-size:20px;margin-right:22px}
.ladder-text{position:absolute;left:566px;top:248px;width:497px;font-size:15px;line-height:34.5px;text-align:justify}

/* Footer */
.site-footer{height:367px;background:var(--black);color:var(--white)}
.site-footer .brand{left:500px;top:44px;width:210px}
.foot-nav{position:absolute;left:0;width:1200px;top:146px;display:flex;justify-content:center;gap:19px}
.foot-nav a{color:var(--white);text-decoration:none;font-size:15px;font-weight:500}
.contact{position:absolute;top:206px}
.contact-icon{position:absolute;left:0;top:10px;width:46px;height:46px;border-radius:50%;background:var(--red-bright);display:flex;align-items:center;justify-content:center}
.contact h4{margin-left:85px;font-family:var(--display);font-weight:400;font-size:22px}
.contact p{margin-left:85px;margin-top:14px;font-size:15px}
.copyright{position:absolute;left:0;width:1200px;top:318px;text-align:center;font-size:15px}
.social{position:absolute;right:22px;top:292px;display:flex;align-items:center;gap:8px;font-size:13px}
.social i{width:40px;height:40px;border-radius:50%;background:var(--white)}
</style>
</head>
<body>

<header class="hero">
  <div class="hero-photo" role="img" aria-label="Dark studio photo of a teal and orange miniature race car on a wooden floor"><div class="hero-car"></div></div>
  <div class="brand"><span class="brand-mark"></span>Rapid Pulse Tiny Track Karts</div>
  <nav class="main-nav">
    <a href="#">HOME</a><a href="#">ABOUT US</a><a href="#">MERCHANDISE</a><a href="#">GALLERY</a><a href="#">SPONSOR</a><a href="#">CONTACT US</a>
  </nav>
  <a class="login">LOG IN</a>
  <div class="welcome">
    <small>WELCOME TO</small>
    <strong>RAPID PULSE TINY</strong>
    <strong>TRACK KARTS</strong>
  </div>
</header>

<section class="calendar">
  <h2 class="section-title">EVENT CALENDAR</h2>
  <div class="pill-btn btn-prev">&larr; PREVIOUS</div>
  <div class="month">OCT 2023</div>
  <div class="pill-btn btn-next">NEXT &rarr;</div>
  <div class="cal-grid">
    <div class="dow">SUN</div><div class="dow">MON</div><div class="dow">TUE</div><div class="dow">WED</div><div class="dow">THU</div><div class="dow">FRI</div><div class="dow">SAT</div>
    <div class="day">01</div><div class="day">02</div><div class="day">03</div><div class="day">04</div><div class="day">05</div><div class="day">06</div><div class="day">07</div>
    <div class="day">08</div><div class="day">09</div><div class="day">10</div><div class="day today"><span>11</span></div><div class="day">12</div><div class="day">13</div><div class="day">14</div>
    <div class="day">15</div><div class="day">16</div><div class="day">17</div><div class="day">18</div><div class="day">19</div><div class="day">20</div><div class="day">21</div>
    <div class="day">22</div><div class="day">23</div><div class="day">24</div><div class="day">25</div><div class="day">26</div><div class="day">27</div><div class="day">28</div>
    <div class="day">29</div><div class="day">30</div><div class="day">31</div><div class="day muted">01</div><div class="day muted">02</div><div class="day muted">03</div><div class="day muted">04</div>
  </div>
</section>

<section class="about on-dark">
  <h2 class="section-title">ABOUT US</h2>
  <div class="about-photo" role="img" aria-label="Black and white photo of a miniature formula car in front of a dark wall"></div>
  <p class="about-text">Lorem ipsum dolor sit amet, consectetur adipiscing elit, sed do eiusmod tempor incididunt ut labore et dolore magna aliqua. Ut enim ad minim veniam, quis nostrud exercitation ullamco laboris nisi ut aliquip ex ea commodo consequat. Duis aute irure dolor in reprehenderit in voluptate velit esse cillum dolore eu fugiat nulla pariatur. Excepteur sint occaecat cupidatat non proident, sunt in culpa qui officia deserunt mollit anim id est laborum.</p>
  <div class="outline-btn">VIEW MORE <span>&rarr;</span></div>
</section>

<section class="merch">
  <h2 class="section-title">MERCHANDISE</h2>
  <div class="round-arrow" style="left:42px;top:345px"><svg width="16" height="16" viewBox="0 0 16 16"><path d="M10 3 5 8l5 5" fill="none" stroke="#fff" stroke-width="2.4" stroke-linecap="round" stroke-linejoin="round"/></svg></div>
  <div class="merch-card" style="left:115px"><div class="merch-photo" role="img" aria-label="Silver miniature race car with warm bokeh lights" style="background:radial-gradient(circle at 40% 30%,#f1b45a,#8a5a2c 45%,#3a2a1e)"></div><div class="merch-name">LOREM IPSUM</div><div class="price">$56.9</div></div>
  <div class="merch-card" style="left:441px"><div class="merch-photo" role="img" aria-label="Racing driver in helmet and orange suit celebrating in a kart" style="background:linear-gradient(180deg,#cbb8a0,#a77a52 50%,#c2541f)"></div><div class="merch-name">LOREM IPSUM</div><div class="price">$45.5</div></div>
  <div class="merch-card" style="left:768px"><div class="merch-photo" role="img" aria-label="Red sports car on a neon-lit city street at night" style="background:linear-gradient(180deg,#1d2838,#3c2c44 50%,#5a1f2a)"></div><div class="merch-name">LOREM IPSUM</div><div class="price">$87.08</div></div>
  <div class="round-arrow" style="left:1116px;top:345px"><svg width="16" height="16" viewBox="0 0 16 16"><path d="M6 3l5 5-5 5" fill="none" stroke="#fff" stroke-width="2.4" stroke-linecap="round" stroke-linejoin="round"/></svg></div>
</section>

<section class="gallery on-dark">
  <h2 class="section-title">GALLERY</h2>
  <div class="gallery-photo" role="img" aria-label="White miniature race car with motion blur" style="left:-10px;top:165px;width:279px;height:330px;background:linear-gradient(180deg,#5a5048,#7d7670 45%,#3b3734)"></div>
  <div class="gallery-photo" role="img" aria-label="Rally car drifting through snow at sunset" style="left:281px;top:180px;width:313px;height:332px;background:linear-gradient(180deg,#2e3a4a,#d38a4a 40%,#9fb6c8 70%,#e9eef2)"></div>
  <div class="gallery-photo" role="img" aria-label="Blue miniature formula car on a slot track" style="left:606px;top:161px;width:313px;height:334px;background:linear-gradient(180deg,#b9c43a,#2e7a4a 45%,#3a3f58 75%,#5a4a3a)"></div>
  <div class="gallery-photo" role="img" aria-label="Dark miniature car on a slot racing track" style="left:933px;top:180px;width:280px;height:332px;background:linear-gradient(180deg,#6a645c,#4a423a 55%,#2a2420)"></div>
  <svg class="abs" style="left:1088px;top:538px" width="90" height="20" viewBox="0 0 90 20"><path d="M32 10H4m8-7-8 7 8 7M58 10h28m-8-7 8 7-8 7" fill="none" stroke="#fff" stroke-width="2" stroke-linecap="round" stroke-linejoin="round"/></svg>
</section>

<section class="sponsor">
  <h2 class="section-title">SPONSOR</h2>
  <div class="sponsor-box" style="left:115px"><svg width="120" height="120"><circle cx="60" cy="60" r="50" fill="#e9842e"/><circle cx="60" cy="60" r="34" fill="#1d3b5a"/></svg></div>
  <div class="sponsor-box" style="left:311px"><svg width="140" height="80"><rect x="10" y="20" width="120" height="40" rx="20" fill="#c8202a"/></svg></div>
  <div class="sponsor-box" style="left:508px"><svg width="120" height="100"><circle cx="60" cy="50" r="42" fill="#f6d21b"/></svg></div>
  <div class="sponsor-box" style="left:704px"><svg width="120" height="120"><rect x="30" y="20" width="60" height="80" rx="12" fill="#1d4f9c"/></svg></div>
  <div class="sponsor-box" style="left:901px"><svg width="140" height="100"><rect x="15" y="30" width="110" height="44" rx="6" fill="#1d2b5a"/></svg></div>
  <span class="dot active" style="left:537px"></span>
  <span class="dot" style="left:584px"></span>
  <span class="dot" style="left:629px"></span>
</section>

<section class="ladder">
  <h2 class="section-title">CHAMPIONSHIP LADDER</h2>
  <div class="ladder-photo" role="img" aria-label="Group photo of the championship team in an office"></div>
  <div class="round-arrow" style="left:107px;top:269px"><svg width="16" height="16" viewBox="0 0 16 16"><path d="M10 3 5 8l5 5" fill="none" stroke="#fff" stroke-width="2.4" stroke-linecap="round" stroke-linejoin="round"/></svg></div>
  <div class="round-arrow" style="left:486px;top:269px"><svg width="16" height="16" viewBox="0 0 16 16"><path d="M6 3l5 5-5 5" fill="none" stroke="#fff" stroke-width="2.4" stroke-linecap="round" stroke-linejoin="round"/></svg></div>
  <p class="ladder-info" style="top:127px"><b>EVENT :</b>Lorem ipsum dolor</p>
  <p class="ladder-info" style="top:186px"><b>YEAR OF THE EVENT :</b>2023</p>
  <p class="ladder-info" style="top:243px"><b>DESCRIPTION :</b></p>
  <p class="ladder-text" style="top:295px">Lorem ipsum dolor sit amet, consectetur adipiscing elit, sed do eiusmod tempor incididunt ut labore et dolore magna aliqua. Ut enim ad minim veniam, quis nostrud exercitation ullamco laboris nisi ut aliquip ex ea commodo consequat. Duis aute irure dolor in reprehenderit in voluptate velit esse</p>
</section>

<footer class="site-footer">
  <div class="brand"><span class="brand-mark"></span>Rapid Pulse Tiny Track Karts</div>
  <nav class="foot-nav">
    <a href="#">HOME</a><a href="#">ABOUT US</a><a href="#">MERCHANDISE</a><a href="#">GALLERY</a><a href="#">SPONSOR</a><a href="#">CONTACT US</a>
  </nav>
  <div class="contact" style="left:111px">
    <span class="contact-icon"><svg width="22" height="22" viewBox="0 0 24 24"><path d="M6.6 10.8a15 15 0 0 0 6.6 6.6l2.2-2.2a1 1 0 0 1 1-.25 11 11 0 0 0 3.6.6 1 1 0 0 1 1 1V20a1 1 0 0 1-1 1A17 17 0 0 1 3 4a1 1 0 0 1 1-1h3.5a1 1 0 0 1 1 1c0 1.25.2 2.45.6 3.6a1 1 0 0 1-.25 1z" fill="#fff"/></svg></span>
    <h4>CALL US:</h4><p>+1 999 999 9999</p>
  </div>
  <div class="contact" style="left:418px">
    <span class="contact-icon"><svg width="24" height="20" viewBox="0 0 24 20"><rect x="2" y="3" width="20" height="14" rx="2" fill="#fff"/><path d="M3 4l9 7 9-7" fill="none" stroke="#f21d1d" stroke-width="2"/></svg></span>
    <h4>MAIL US:</h4><p>RAPIDPULSEKARTS@MAILBOX.COM</p>
  </div>
  <div class="contact" style="left:844px">
    <span class="contact-icon"><svg width="20" height="24" viewBox="0 0 20 24"><path d="M10 1a8 8 0 0 0-8 8c0 6 8 14 8 14s8-8 8-14a8 8 0 0 0-8-8z" fill="#fff"/><circle cx="10" cy="9" r="3" fill="#f21d1d"/></svg></span>
    <h4>REACH US:</h4><p>54, Lorem Lipsum</p>
  </div>
  <p class="copyright">@2023 COPYRIGHTS. RAPID PULSE TINY TRACK KARTS. ALL RIGHTS RESERVED</p>
  <div class="social"><span>clip wave</span><i></i></div>
</footer>

</body>
</html>
```